Brintel Wireless generic phone package design

Hello, We are a new wireless carrier and we need a simple but impressive looking design for our generic Brintel Wireless phone box. I have included a box design idea we've been playing with, just to show the simplicity of it. Dimension of the box should 4.5x7.5x2 inches. We do have a website if you'd like to look at our company, attached a few pictures, our Logo and a the wallpaper we like to use. Our slogan is " Now I Can REALLY Hear You!" that we'd like to have on the box, the logo as well and our website address "brintelwireless.example". Just a few things to mention that are important in the design. Of course if you have great vision and would like to provide us with a great design completely different from what we've envisioned would love to see it as well.
Orr website is www.brintelwireless.example, please feel free to visit the site for some ideas. Thank you

Reason: I wanted to extend current deadline due to limited response so far. I can have the project due date extended til Nov 5th , I also need to make dessision by then. I'd like to get a few more ideas before picking the perfect design for our soft launch. Thank you

Industry/Entity Type

Telecommunications

Font styles to use
Serif

Requirements
Must have
• Logo
• brintelwireless.example
• Now I Can REALLY Hear You!
Should not have
• Address or phone number

```html
<!DOCTYPE html>
<html lang="en">
<head>
<meta charset="utf-8">
<title>Brintel Wireless – Phone Box Panels</title>
<link href="https://fonts.googleapis.com/css2?family=Oswald:wght@500;600&family=Roboto:wght@500&display=swap" rel="stylesheet">
<style>
  :root {
    --stage: #e7eaee;
    --photo-light: #e9e3dc;
    --photo-warm: #b99a7c;
    --accent-red: #e3232b;
    --strip-grey: #2e2d2f;
    --panel-black: #1f1d1e;
    --headline-white: #f2f2f2;
    --brand-grey: #c4c4c4;
    --side-red-top: #7a0a12;
    --side-red-bottom: #4e0308;
  }
  * { margin: 0; padding: 0; box-sizing: border-box; }
  html, body {
    width: 1122px;
    height: 1200px;
    overflow: hidden;
    background: var(--stage);
  }
  .box-front {
    position: absolute;
    left: 99px;
    top: 67px;
    width: 640px;
    height: 1066px;
    background: var(--strip-grey);
    overflow: hidden;
  }
  .box-side {
    position: absolute;
    left: 739px;
    top: 67px;
    width: 284px;
    height: 1066px;
    background: linear-gradient(180deg, var(--side-red-top) 0%, var(--side-red-bottom) 100%);
  }
  .lifestyle-photo {
    position: absolute;
    left: 0; top: 0;
    width: 100%;
    height: 420px;
    background: linear-gradient(110deg, var(--photo-warm) 0%, var(--photo-light) 45%, #f4f1ee 75%, var(--photo-warm) 100%);
  }
  .accent-rule {
    position: absolute;
    left: 0; top: 420px;
    width: 100%;
    height: 7px;
    background: var(--accent-red);
  }
  .side-strip {
    position: absolute;
    top: 427px;
    bottom: 0;
    width: 106px;
    background: linear-gradient(180deg, #353436 0%, var(--strip-grey) 100%);
  }
  .side-strip--left { left: 0; }
  .side-strip--right { right: 0; }
  .message-panel {
    position: absolute;
    left: 106px;
    right: 106px;
    top: 427px;
    bottom: 0;
    background: var(--panel-black);
    text-align: center;
  }
  .slogan {
    font-family: "Oswald", sans-serif;
    font-weight: 600;
    text-transform: uppercase;
    line-height: 0.98;
    margin-top: 54px;
  }
  .slogan span { display: block; }
  .slogan__lead { font-size: 72px; color: var(--headline-white); }
  .slogan__emphasis { font-size: 102px; color: var(--headline-white); }
  .slogan__close { font-size: 77px; color: var(--accent-red); }
  .brand-signoff {
    position: absolute;
    left: 0; right: 0;
    display: flex;
    flex-direction: column;
    align-items: center;
    gap: 16px;
  }
  .message-panel .brand-signoff { bottom: 92px; }
  .box-side .brand-signoff { top: 448px; }
  .brand-signoff__mark {
    width: 76px; height: 76px;
    border-radius: 50%;
    background: var(--accent-red);
  }
  .box-side .brand-signoff__mark { width: 60px; height: 60px; background: var(--brand-grey); }
  .brand-signoff__name {
    font-family: "Roboto", sans-serif;
    font-weight: 500;
    font-size: 28px;
    color: var(--brand-grey);
  }
  .box-side .brand-signoff__name { font-size: 22px; }
</style>
</head>
<body>
  <main class="box-front">
    <div class="lifestyle-photo" role="img" aria-label="Smiling woman relaxing on a sofa while talking on her mobile phone in a bright living room"></div>
    <div class="accent-rule"></div>
    <div class="side-strip side-strip--left" role="img" aria-label="Faint repeating pattern of phone outlines"></div>
    <div class="side-strip side-strip--right" role="img" aria-label="Faint repeating pattern of phone outlines"></div>
    <section class="message-panel">
      <h1 class="slogan">
        <span class="slogan__lead">Now I Can</span>
        <span class="slogan__emphasis">Really</span>
        <span class="slogan__close">Hear You!</span>
      </h1>
      <div class="brand-signoff">
        <span class="brand-signoff__mark"></span>
        <span class="brand-signoff__name">brintelwireless.example</span>
      </div>
    </section>
  </main>
  <aside class="box-side">
    <div class="brand-signoff">
      <span class="brand-signoff__mark"></span>
      <span class="brand-signoff__name">brintelwireless.example</span>
    </div>
  </aside>
</body>
</html>
```